We are a recruitment company based in Norwich/Cambridge England.
I have included our company logo which we want to remain the same.

What we are looking for is a new creative Business card which will really stand out!!

Contact Information for Business Card

Harriet Dunmore
email: Harriet@plavex.co.uk
Address: Brackwell House
Fenmoor Enterprise Park
Partridge Way
Norwich
QB9 3KX
Tel:01632 960418

```html
<!DOCTYPE html>
<html lang="en">
<head>
<meta charset="utf-8">
<title>Plavex Business Card</title>
<link href="https://fonts.googleapis.com/css2?family=Montserrat:wght@700&family=Lato:wght@400;700&display=swap" rel="stylesheet">
<style>
  :root {
    --brand-green: #8cc63f;
    --card-white: #eeeeee;
    --ink-white: #ffffff;
    --brand-grey: #8a898c;
    --stage: #f4f4f2;
  }
  html, body {
    margin: 0;
    padding: 0;
    width: 1200px;
    height: 900px;
    overflow: hidden;
    background: var(--stage);
  }
  .canvas {
    position: relative;
    width: 1200px;
    height: 900px;
  }
  .card {
    position: absolute;
    overflow: hidden;
    box-shadow: 0 6px 18px rgba(0,0,0,0.12);
  }
  .card-front {
    left: 78px;
    top: 34px;
    width: 588px;
    height: 364px;
    background: var(--brand-green);
    color: var(--ink-white);
    font-family: "Lato", sans-serif;
  }
  .front-disc {
    position: absolute;
    right: -150px;
    top: 62px;
    width: 360px;
    height: 360px;
    border-radius: 50%;
    background: var(--ink-white);
  }
  .holder-name {
    position: absolute;
    left: 40px;
    top: 50px;
    margin: 0;
    font-family: "Montserrat", sans-serif;
    font-weight: 700;
    font-size: 21px;
    letter-spacing: 0.3px;
    text-transform: uppercase;
  }
  .holder-role {
    position: absolute;
    left: 40px;
    top: 73px;
    margin: 0;
    font-size: 16px;
  }
  .contact-list {
    position: absolute;
    left: 40px;
    top: 171px;
    margin: 0;
    padding: 0;
    list-style: none;
    font-size: 15.5px;
    line-height: 21.5px;
  }
  .contact-list li {
    display: flex;
    align-items: center;
    gap: 6px;
  }
  .contact-icon {
    width: 12px;
    height: 12px;
    fill: var(--ink-white);
    flex: none;
  }
  .postal-address {
    position: absolute;
    left: 40px;
    top: 286px;
    margin: 0;
    font-style: normal;
    font-size: 15.5px;
    line-height: 23px;
  }
  .card-back {
    left: 389px;
    top: 505px;
    width: 566px;
    height: 352px;
    background: var(--card-white);
    font-family: "Lato", sans-serif;
  }
  .brand-lockup {
    position: absolute;
    left: 88px;
    top: 122px;
    display: flex;
    align-items: center;
    gap: 16px;
  }
  .brand-dot {
    width: 70px;
    height: 70px;
    border-radius: 50%;
    background: var(--brand-green);
  }
  .brand-text {
    display: flex;
    flex-direction: column;
  }
  .brand-name {
    font-weight: 700;
    font-size: 52px;
    line-height: 52px;
    color: var(--brand-grey);
  }
  .brand-tagline {
    font-size: 11.5px;
    letter-spacing: 3px;
    color: var(--brand-grey);
    margin-top: 2px;
  }
  .back-web {
    position: absolute;
    left: 0;
    right: 0;
    top: 297px;
    text-align: center;
    font-weight: 700;
    font-size: 15px;
    color: var(--brand-green);
  }
</style>
</head>
<body>
<main class="canvas">
  <section class="card card-front">
    <div class="front-disc"></div>
    <h1 class="holder-name">Harriet Dunmore</h1>
    <p class="holder-role">Managing Director</p>
    <ul class="contact-list">
      <li>
        <svg class="contact-icon" viewBox="0 0 12 12" aria-hidden="true"><path d="M1 4c0-2 1-3 5-3s5 1 5 3l-2 1-1-2H4L3 5zM3 6h6l1 5H2z"/></svg>
        01632 960418
      </li>
      <li>
        <svg class="contact-icon" viewBox="0 0 12 12" aria-hidden="true"><path d="M1 2h10v8H1z M2 3v6l4-3z M10 3v6L6 6z" fill-rule="evenodd"/></svg>
        Harriet@plavex.co.uk
      </li>
      <li>
        <svg class="contact-icon" viewBox="0 0 12 12" aria-hidden="true"><circle cx="6" cy="6" r="5.5"/></svg>
        www.plavex.co.uk
      </li>
    </ul>
    <address class="postal-address">
      Brackwell House, Fenmoor Enterprise Park,<br>
      Partridge Way, Norwich, QB9 3KX
    </address>
  </section>

  <section class="card card-back">
    <div class="brand-lockup">
      <div class="brand-dot"></div>
      <div class="brand-text">
        <span class="brand-name">Plavex</span>
        <span class="brand-tagline">Technology Recruitment</span>
      </div>
    </div>
    <div class="back-web">www.plavex.co.uk</div>
  </section>
</main>
</body>
</html>
```